AUTO SPAREPART DISTRIBUTOR BUSINESS CARD

Our company need a business card design. We are a distributor and importer of car spareparts for VORN and PELTARO car model. We would like the design with White color back ground and attractive color for the fonts and looks clean, simple and attractive.
We provide the company information and the brand logo (VORN, PELTARO, ZUM, 738) should be put on the business card.

Thank you

Target Market(s)

Auto spareparts retailer shop and supplier.

Industry/Entity Type

Business

Contact Information for Business Card

The front side of the business card only contain company informations, and the back side may be put the brand logo (VORN, PELTARO, ZUM AND 738).

Requirements
Must have
• On the back side ( the brand logo) position , should have a transparency world map picture ( i uploaded the world map picture sample ).
• Also, need to put some words of " AUTO PARTS DISTRIBUTOR " (may be put on any appropriate place).

```html
<!DOCTYPE html>
<html lang="en">
<head>
<meta charset="utf-8">
<title>PT.Veranta Inter Global – Business Card</title>
<link rel="stylesheet" href="https://fonts.googleapis.com/css2?family=Open+Sans:wght@400;600;700&family=Oswald:wght@500;600&display=swap">
<style>
  :root {
    --bg: #ebe8e3;
    --card: #ffffff;
    --green-dark: #5f9433;
    --green: #6fa63c;
    --green-light: #7db544;
    --green-pale: #86bd4a;
    --map-tint: #cfd8c4;
    --ink: #333333;
    --ink-soft: #555555;
    --brand-red: #c8202c;
    --brand-blue: #1f4f9c;
    --brand-dark: #3a3a3a;
    --shadow: 0 8px 24px rgba(0,0,0,.18);
  }
  * { box-sizing: border-box; margin: 0; padding: 0; }
  html, body { width: 1200px; height: 900px; overflow: hidden; }
  body {
    background: var(--bg);
    font-family: "Open Sans", Arial, sans-serif;
    color: var(--ink);
    position: relative;
  }
  .card {
    position: absolute;
    left: 250px;
    width: 700px;
    height: 400px;
    background: var(--card);
    box-shadow: var(--shadow);
    overflow: hidden;
  }
  .card--front { top: 35px; }
  .card--back  { top: 465px; }

  /* Front card */
  .front__band {
    position: absolute; inset: 0 0 100px 0;
    background: var(--green);
  }
  .front__band svg { position: absolute; inset: 0; width: 100%; height: 100%; }
  .front__title {
    position: absolute; left: 0; right: 0; top: 104px;
    display: flex; align-items: center; justify-content: center; gap: 18px;
    color: #fff;
  }
  .front__mark { width: 46px; height: 46px; background: #fff; flex: none; }
  .front__name {
    font-family: "Oswald", "Arial Narrow", sans-serif;
    font-weight: 600; font-size: 44px; letter-spacing: .5px; line-height: 1.1;
  }
  .front__tagline {
    position: absolute; left: 0; right: 0; top: 178px;
    text-align: center; color: #fff;
    font-family: "Oswald", "Arial Narrow", sans-serif;
    font-weight: 500; font-size: 17px; letter-spacing: 5px;
  }
  .brand-strip {
    position: absolute; left: 0; right: 0; bottom: 0; height: 100px;
    display: flex; align-items: center; justify-content: space-around;
    padding: 0 40px;
  }
  .brand-strip__map {
    position: absolute; inset: 8px 60px;
    background:
      radial-gradient(ellipse 18% 45% at 22% 45%, var(--map-tint) 0 60%, transparent 62%),
      radial-gradient(ellipse 10% 40% at 33% 75%, var(--map-tint) 0 60%, transparent 62%),
      radial-gradient(ellipse 22% 40% at 60% 40%, var(--map-tint) 0 60%, transparent 62%),
      radial-gradient(ellipse 9% 38% at 52% 72%, var(--map-tint) 0 60%, transparent 62%),
      radial-gradient(ellipse 8% 22% at 82% 80%, var(--map-tint) 0 60%, transparent 62%);
    opacity: .55;
  }
  .brand { position: relative; text-align: center; font-weight: 700; font-size: 26px; line-height: 1; }
  .brand--738 { color: var(--brand-red); }
  .brand--zum { color: var(--brand-dark); }
  .brand--vorn { color: var(--brand-red); }
  .brand--peltaro { color: var(--brand-blue); }
  .brand__sub { display: block; font-size: 9px; font-weight: 400; color: var(--ink-soft); margin-top: 6px; }

  /* Back card */
  .back__identity {
    position: absolute; left: 40px; top: 150px; width: 300px;
    display: flex; align-items: center; justify-content: center; gap: 14px;
  }
  .back__mark { width: 38px; height: 38px; background: var(--green-light); flex: none; }
  .back__company { font-weight: 700; font-size: 40px; color: var(--green-dark); }
  .chat-id {
    position: absolute; left: 115px; top: 318px;
    display: flex; align-items: center; gap: 10px;
    font-size: 22px; color: var(--ink);
  }
  .chat-id__dot { width: 26px; height: 26px; border-radius: 50%; background: var(--green-light); }
  .person { position: absolute; left: 380px; top: 36px; }
  .person__name { font-weight: 700; font-size: 22px; color: var(--green-light); }
  .person__role { font-size: 15px; color: var(--ink); margin: 2px 0 0 10px; }
  .address {
    font-size: 15px; line-height: 1.35; color: var(--ink-soft);
    margin: 32px 0 0 40px; font-style: normal;
  }
  .contacts { list-style: none; margin: 24px 0 0 40px; font-size: 16px; line-height: 1.45; color: var(--ink); }
  .contacts li { display: flex; align-items: center; gap: 10px; }
  .contacts svg { width: 13px; height: 13px; fill: var(--green-light); flex: none; }
</style>
</head>
<body>

<section class="card card--front" aria-label="Business card front">
  <div class="front__band">
    <svg viewBox="0 0 700 300" preserveAspectRatio="none" aria-hidden="true">
      <polygon points="0,0 220,0 110,300 0,300" fill="var(--green-dark)" opacity=".35"/>
      <polygon points="330,0 700,0 700,150 500,60" fill="var(--green-light)" opacity=".6"/>
      <polygon points="260,300 520,120 700,180 700,300" fill="var(--green-pale)" opacity=".55"/>
      <polygon points="420,40 620,120 470,200" fill="var(--green-dark)" opacity=".25"/>
    </svg>
    <div class="front__title">
      <span class="front__mark" aria-hidden="true"></span>
      <h1 class="front__name">PT.VERANTA INTER GLOBAL</h1>
    </div>
    <p class="front__tagline">AUTO PARTS DISTRIBUTOR</p>
  </div>
  <div class="brand-strip">
    <div class="brand-strip__map" role="img" aria-label="Transparent world map behind the partner brands"></div>
    <div class="brand brand--738">738<span class="brand__sub">Original Parts</span></div>
    <div class="brand brand--zum">ZUM</div>
    <div class="brand brand--vorn">VORN</div>
    <div class="brand brand--peltaro">PELTARO</div>
  </div>
</section>

<section class="card card--back" aria-label="Business card back">
  <div class="back__identity">
    <span class="back__mark" aria-hidden="true"></span>
    <span class="back__company">VERANTA</span>
  </div>
  <div class="chat-id"><span class="chat-id__dot" aria-hidden="true"></span>ari.santo22</div>

  <div class="person">
    <h2 class="person__name">ARI SANTO</h2>
    <p class="person__role">Director</p>
    <address class="address">
      Taman Sari Residence 4 ,<br>
      Blok c-07 No.B-9 ,<br>
      Kedoya, Jakarta<br>
      Barat, Indonesia (11520).
    </address>
    <ul class="contacts">
      <li><svg viewBox="0 0 16 16" aria-hidden="true"><path d="M3 1l3 3-2 2c1 2 3 4 5 5l2-2 3 3-2 3C6 15 1 10 0 4z"/></svg>+62-21-55318204</li>
      <li><svg viewBox="0 0 16 16" aria-hidden="true"><path d="M4 1h7v4H4zM1 6h14v7h-3v2H4v-2H1zm4 5v3h6v-3z"/></svg>+62-21-55318210</li>
      <li><svg viewBox="0 0 16 16" aria-hidden="true"><path d="M4 0h8v16H4zm1 2v10h6V2z"/></svg>+62-812740319</li>
      <li><svg viewBox="0 0 16 16" aria-hidden="true"><path d="M0 3h16v10H0zm1 1l7 5 7-5z"/></svg>veranta-indonesia@mailbox.com</li>
    </ul>
  </div>
</section>

</body>
</html>
```